Need a website to promote and sell my book

Using images from the book, I need a website designed that helps promote the book and eventually sell it.
*Need a landing page
*About the author page
*Storefront page to purchase
*Coming soon page
*"Featured in" page that can link to news articles etc.
The images posted here are examples, the winner of the contest will get the images from the finished book. I will provide the exact text to the winner of the contest.

I can also provide images of kids reading the book. For now, I'll just use one, the winner can have them all to choose from.
Updates

Extending deadline to allow for a few more designers to submit and to allow time for me to review and hold a poll

Target Market(s)

Parents, aunts, uncles, grandparents, friends who have kids; teachers, daycare teachers, babysitters etc.

Industry/Entity Type

Custom Publishing

Coding

Coded - Design and coding required

Number of Pages Required

5+ page

Font styles to use
Sans Serif

Colors

Designer to choose colors to be used in the design.

Requirements
Must have
• It must have a fun feel like the book.
Nice to have
• Would be great to have a section that automatically pulls tweets about the book into it.

```html
<!DOCTYPE html>
<html lang="en">
<head>
<meta charset="utf-8">
<title>Little Lab Adventures</title>
<link href="https://fonts.googleapis.com/css2?family=Poppins:wght@400;500;600;700;800&family=Dancing+Script:wght@600&display=swap" rel="stylesheet">
<style>
  :root{
    --sun:#f5b84a;
    --sun-deep:#f2a93b;
    --sky:#5ec6e8;
    --sky-light:#8fd8f0;
    --sky-deep:#3fb2dc;
    --coral:#f2645f;
    --coral-light:#f7928a;
    --ink:#2e2e33;
    --muted:#6d6f75;
    --white:#ffffff;
    --paper:#ffffff;
    --red:#e94a3f;
  }
  *{box-sizing:border-box;margin:0;padding:0}
  html,body{width:1200px;height:3824px;overflow:hidden}
  body{font-family:"Poppins",sans-serif;color:var(--ink);background:var(--paper);position:relative}
  .section{position:absolute;left:0;width:1200px}
  .wave{position:absolute;left:0;width:1200px;display:block}
  .btn{display:inline-block;background:var(--sky);color:var(--white);font-weight:600;font-size:15px;padding:13px 34px;border-radius:30px;box-shadow:0 6px 14px rgba(0,0,0,.12);white-space:nowrap}
  .placeholder{position:absolute;display:block}

  /* Hero */
  .hero{top:0;height:820px;background:linear-gradient(180deg,var(--sun) 0%,var(--sun-deep) 100%)}
  .brand{position:absolute;left:100px;top:36px;width:160px;font-weight:800;font-size:26px;line-height:1.05;color:var(--red)}
  .nav{position:absolute;left:600px;top:26px;display:flex;gap:6px;white-space:nowrap}
  .nav a{color:var(--white);font-size:14px;font-weight:500;padding:10px 18px;border-radius:22px;text-decoration:none;white-space:nowrap}
  .nav a.active{background:var(--white);color:var(--sun-deep)}
  .hero-title{position:absolute;left:100px;top:318px;font-size:42px;font-weight:700;color:var(--white);line-height:1.2}
  .hero-text{position:absolute;left:100px;top:432px;width:340px;font-size:14px;color:var(--white);line-height:1.55}
  .hero .btn{position:absolute;left:100px;top:500px}

  /* About */
  .about{top:760px;height:560px;background:var(--sky)}
  .about-title{position:absolute;left:580px;top:110px;font-size:62px;font-weight:700;color:var(--white)}
  .about-text{position:absolute;left:580px;top:200px;width:500px;font-size:14px;color:var(--white);line-height:1.6}
  .signature{position:absolute;left:580px;top:320px;font-family:"Dancing Script",cursive;font-size:34px;color:var(--white)}
  .degree{position:absolute;left:580px;top:372px;font-size:12px;font-weight:600;color:var(--white)}

  /* Featured */
  .featured{top:1320px;height:880px;background:var(--paper)}
  .featured-title{position:absolute;left:0;width:1200px;top:40px;text-align:center;font-size:70px;font-weight:700;color:var(--ink)}
  .featured-sub{position:absolute;left:390px;top:145px;width:420px;text-align:center;font-size:14px;color:var(--muted);line-height:1.55}
  .cards{position:absolute;left:90px;top:240px;display:flex;gap:60px}
  .card{width:300px;position:relative}
  .card-photo{width:290px;height:220px;border-radius:6px;position:relative;z-index:1}
  .card-frame{position:absolute;left:14px;top:-12px;width:290px;height:220px;border:4px solid var(--sky);border-radius:8px}
  .card-date{margin-top:18px;font-size:12px;color:var(--muted)}
  .card-title{font-size:22px;font-weight:700;margin-top:2px}
  .card-text{font-size:13px;color:var(--muted);line-height:1.55;margin-top:8px}
  .card-link{display:block;margin-top:12px;font-size:13px;font-weight:600;color:var(--sky-deep)}
  .featured .btn{position:absolute;left:520px;top:710px}

  /* Store */
  .store{top:2200px;height:640px;background:linear-gradient(180deg,var(--sky-light),var(--sky))}
  .store-title{position:absolute;left:90px;top:120px;font-size:66px;font-weight:700;color:var(--white)}
  .store-text{position:absolute;left:90px;top:220px;width:460px;font-size:14px;color:var(--white);line-height:1.6}
  .store .btn{position:absolute;left:90px;top:330px}

  /* Coming soon */
  .coming{top:2800px;height:560px;background:linear-gradient(180deg,var(--coral-light),var(--coral))}
  .coming-title{position:absolute;left:450px;top:140px;font-size:60px;font-weight:700;color:var(--white);line-height:1.05;white-space:nowrap}
  .coming-title span{display:block;font-size:112px}
  .coming-text{position:absolute;left:450px;top:380px;width:400px;font-size:14px;color:var(--white);line-height:1.55}

  /* Newsletter + footer */
  .contact{top:3320px;height:504px;background:linear-gradient(180deg,var(--sky-light),var(--sky-deep))}
  .contact-title{position:absolute;left:0;width:1200px;top:110px;text-align:center;font-size:38px;font-weight:700;color:var(--white);line-height:1.2}
  .signup{position:absolute;left:340px;top:240px;width:520px;height:54px;background:var(--white);border-radius:30px}
  .signup-input{position:absolute;left:28px;top:17px;font-size:14px;color:var(--muted)}
  .signup-btn{position:absolute;right:4px;top:4px;height:46px;width:140px;border-radius:24px;background:var(--sky-deep);color:var(--white);font-weight:600;font-size:14px;text-align:center;line-height:46px}
  .footer-nav{position:absolute;left:90px;top:388px;display:flex;gap:44px;font-size:14px;font-weight:500;color:var(--white);white-space:nowrap}
  .social{position:absolute;right:90px;top:378px;display:flex;gap:14px}
  .social span{width:38px;height:38px;border-radius:50%;background:var(--white);display:block}
  .copyright{position:absolute;left:0;width:1200px;top:460px;text-align:center;font-size:12px;color:var(--white)}
</style>
</head>
<body>

<section class="section hero">
  <div class="brand">Little Lab Adventures</div>
  <nav class="nav">
    <a class="active">Home</a><a>About</a><a>Storefront</a><a>Coming Soon</a><a>Featured</a>
  </nav>
  <h1 class="hero-title">Today's Research<br>Tomorrow's Innovation</h1>
  <p class="hero-text">Learn to see the world as a lab, one bright idea at a time.</p>
  <span class="btn">Read More</span>
  <div class="placeholder" role="img" aria-label="Book cover front and back, with colourful chemistry illustrations" style="left:620px;top:120px;width:460px;height:470px;border-radius:8px;background:linear-gradient(135deg,#7fd0ee,#f4c64f 60%,#e9573f)"></div>
  <div class="placeholder" role="img" aria-label="Line illustration of a microscope" style="left:60px;top:590px;width:100px;height:150px;border-radius:10px;background:linear-gradient(180deg,rgba(255,255,255,.55),rgba(94,198,232,.6))"></div>
</section>

<section class="section about">
  <svg class="wave" style="top:-60px" height="120" viewBox="0 0 1200 120" preserveAspectRatio="none"><path d="M0 60 C200 0 350 120 600 60 C850 0 1000 110 1200 50 L1200 120 L0 120 Z" fill="#5ec6e8"/></svg>
  <div class="placeholder" role="img" aria-label="Illustrated portrait of the author" style="left:110px;top:60px;width:340px;height:300px;border-radius:48% 52% 45% 55%;background:linear-gradient(135deg,#ffffff,#f3d7c6 55%,#c8613c)"></div>
  <h2 class="about-title">About Author</h2>
  <p class="about-text">This book was inspired by my son and a lifelong love of chemistry. It is designed to introduce young learners to simple ideas and vocabulary using everyday objects. I hope it helps parents and teachers share the wonder of science together, one page and one question at a time.</p>
  <div class="signature">Marisa Vale</div>
  <div class="degree">Ph.D</div>
  <svg class="wave" style="top:480px" height="100" viewBox="0 0 1200 100" preserveAspectRatio="none"><path d="M0 40 C250 100 450 0 700 40 C900 70 1050 20 1200 40 L1200 100 L0 100 Z" fill="#ffffff"/></svg>
</section>

<section class="section featured">
  <h2 class="featured-title">Featured In</h2>
  <p class="featured-sub">Stories, interviews and reviews from readers and press who have shared the book with young scientists.</p>
  <div class="cards">
    <article class="card">
      <div class="card-frame"></div>
      <div class="card-photo" role="img" aria-label="Photo of a child reading the book on a sofa" style="background:linear-gradient(135deg,#b9b3ac,#6f6a66)"></div>
      <div class="card-date">Nov 24, 2019</div>
      <h3 class="card-title">Quisque Accumsan</h3>
      <p class="card-text">A young reader explores the first chapter at home and shares a favourite experiment with family and friends after school today.</p>
      <span class="card-link">Read More</span>
    </article>
    <article class="card">
      <div class="card-frame"></div>
      <div class="card-photo" role="img" aria-label="Photo of a smiling child holding the book" style="background:linear-gradient(135deg,#e7e2dc,#9c8f86)"></div>
      <div class="card-date">Nov 24, 2019</div>
      <h3 class="card-title">Praesent Dapibus</h3>
      <p class="card-text">A curious reader holds the new book proudly and talks about the bright pages, simple words and fun science facts inside.</p>
      <span class="card-link">Read More</span>
    </article>
    <article class="card">
      <div class="card-frame"></div>
      <div class="card-photo" role="img" aria-label="Photo of a child reading the book in a kitchen" style="background:linear-gradient(135deg,#8a7a6b,#3f3a36)"></div>
      <div class="card-date">Nov 24, 2019</div>
      <h3 class="card-title">Nulla Accumsan</h3>
      <p class="card-text">A family reads together in the kitchen and turns everyday items into small experiments that spark big questions about the world.</p>
      <span class="card-link">Read More</span>
    </article>
  </div>
  <span class="btn">View All News Articles</span>
</section>

<section class="section store">
  <svg class="wave" style="top:-40px" height="100" viewBox="0 0 1200 100" preserveAspectRatio="none"><path d="M0 50 C220 0 420 90 650 45 C880 0 1030 80 1200 40 L1200 100 L0 100 Z" fill="#8fd8f0"/></svg>
  <h2 class="store-title">Store Front</h2>
  <p class="store-text">Order signed copies, classroom bundles and gift sets directly from our shop with fast and friendly delivery.</p>
  <span class="btn">Read More</span>
  <div class="placeholder" role="img" aria-label="Photo of a bright bookshop interior with shelves" style="left:660px;top:100px;width:440px;height:360px;background:linear-gradient(180deg,#f3efe8,#c9b89c 70%,#8a7257)"></div>
</section>

<section class="section coming">
  <svg class="wave" style="top:-50px" height="110" viewBox="0 0 1200 110" preserveAspectRatio="none"><path d="M0 60 C200 10 400 100 620 55 C850 10 1020 90 1200 40 L1200 110 L0 110 Z" fill="#f7928a"/></svg>
  <div class="placeholder" role="img" aria-label="Stack of the upcoming book with a colourful chemistry cover" style="left:60px;top:60px;width:330px;height:380px;border-radius:8px;background:linear-gradient(135deg,#7fd0ee,#f4c64f 60%,#e9573f)"></div>
  <h2 class="coming-title">Coming Soon<span>Book</span></h2>
  <p class="coming-text">The next adventure in the series is on its way, full of new experiments to try.</p>
  <div class="placeholder" role="img" aria-label="Photo of a young child standing and reading the book" style="left:940px;top:40px;width:220px;height:470px;border-radius:40px;background:linear-gradient(180deg,#d9c7b4,#5f7a8f 60%,#3d4b59)"></div>
</section>

<section class="section contact">
  <svg class="wave" style="top:-50px" height="110" viewBox="0 0 1200 110" preserveAspectRatio="none"><path d="M0 40 C260 100 480 10 720 55 C930 95 1060 30 1200 50 L1200 110 L0 110 Z" fill="#8fd8f0"/></svg>
  <h2 class="contact-title">Get More News And<br>Be In Touch</h2>
  <div class="signup">
    <span class="signup-input">Enter your email</span>
    <span class="signup-btn">Subscribe</span>
  </div>
  <nav class="footer-nav"><span>Home</span><span>About</span><span>Storefront</span><span>Coming Soon</span><span>Featured</span></nav>
  <div class="social" aria-label="Social links"><span></span><span></span><span></span></div>
  <p class="copyright">© 2019 Little Lab Adventures. All Rights Reserved.</p>
</section>

</body>
</html>
```